HearthMile business card and stationary design

We are looking for a simple yet elegant design for our mortgage company business card and stationary.

The card should include:
Name (Marcus Pell)
Title (CEO)
Phone Number (503-555-0182)
Address (48 Birchwell Court, Suite 314, Ashgrove, OR 97999)
Email (email@hearthmile.example)
"NMLS" i.e. (NMLS 61947)
"Company NMLS" (Company NMLS 274615)

Contact Information for Business Card

See above

```html
<!DOCTYPE html>
<html lang="en">
<head>
<meta charset="utf-8">
<title>HearthMile Business Card</title>
<link rel="stylesheet" href="https://fonts.googleapis.com/css2?family=Montserrat:wght@400;500;600;700&display=swap">
<style>
  :root {
    --navy: #1a2533;
    --blue: #29a8e0;
    --white: #ffffff;
    --ink: #1f2a36;
    --backdrop: #c4c4c4;
  }
  * { margin: 0; padding: 0; box-sizing: border-box; }
  html, body {
    width: 1200px; height: 788px; overflow: hidden;
    background: var(--backdrop);
    font-family: "Montserrat", Arial, sans-serif;
  }
  .canvas { position: relative; width: 1200px; height: 788px; }
  .card {
    position: absolute; left: 330px;
    width: 540px; height: 309px;
    border-radius: 28px; overflow: hidden;
    box-shadow: 0 10px 24px rgba(0,0,0,0.25);
  }
  .card--front { top: 48px; background: var(--white); }
  .card--back { top: 431px; background: var(--navy); }

  .front-waves { position: absolute; inset: 0; width: 540px; height: 309px; }

  .holder { position: absolute; right: 30px; top: 18px; text-align: right; }
  .holder__name {
    color: var(--blue); font-weight: 700; font-size: 19px; letter-spacing: 2px;
    text-transform: uppercase; line-height: 1;
  }
  .holder__title {
    color: var(--white); font-size: 9px; font-weight: 500; letter-spacing: 1px; margin-top: 4px;
  }

  .brand {
    position: absolute; left: 122px; top: 168px;
    color: var(--ink); font-weight: 600; font-size: 30px; letter-spacing: 0.5px; line-height: 1;
  }

  .contact {
    position: absolute; left: 116px; top: 214px; list-style: none;
    color: var(--ink); font-size: 10.5px; line-height: 14px;
  }
  .contact li { display: flex; align-items: center; gap: 5px; }
  .contact .plain { padding-left: 13px; }
  .contact svg { width: 8px; height: 8px; flex: none; }

  .licence {
    position: absolute; right: 28px; top: 168px; text-align: right;
    color: var(--ink); font-size: 10.5px; line-height: 15px;
  }

  .brand--back {
    position: absolute; left: 0; right: 0; top: 50%; transform: translateY(-50%);
    text-align: center; color: var(--white); font-weight: 600; font-size: 60px; letter-spacing: 1px;
  }
</style>
</head>
<body>
<main class="canvas">
  <section class="card card--front">
    <svg class="front-waves" viewBox="0 0 540 309" aria-hidden="true">
      <path d="M0,0 H540 V55 C400,62 250,90 150,130 C90,155 50,200 40,309 H0 Z" fill="var(--navy)"/>
      <path d="M540,68 C400,76 255,104 160,142 C100,167 65,210 58,309" fill="none" stroke="var(--blue)" stroke-width="5"/>
      <path d="M500,60 C380,68 245,92 142,128 C88,150 52,182 30,232" fill="none" stroke="var(--white)" stroke-width="1.6"/>
    </svg>

    <div class="holder">
      <p class="holder__name">Marcus Pell</p>
      <p class="holder__title">CEO</p>
    </div>

    <p class="brand">HearthMile</p>

    <ul class="contact">
      <li class="plain">48 Birchwell Court, Suite 314,</li>
      <li class="plain">Ashgrove, OR 97999</li>
      <li>
        <svg viewBox="0 0 8 8"><path d="M1.5,0.8 L3,0.8 L3.4,2.5 L2.5,3.2 C3,4.3 3.7,5 4.8,5.5 L5.5,4.6 L7.2,5 L7.2,6.5 C4,6.8 1.2,4 1.5,0.8 Z" fill="var(--blue)"/></svg>
        503-555-0182
      </li>
      <li>
        <svg viewBox="0 0 8 8"><rect x="0.5" y="1.5" width="7" height="5" fill="var(--blue)"/><path d="M0.5,1.5 L4,4.3 L7.5,1.5" fill="none" stroke="var(--white)" stroke-width="0.8"/></svg>
        email@hearthmile.example
      </li>
      <li>
        <svg viewBox="0 0 8 8"><circle cx="4" cy="4" r="3.5" fill="var(--blue)"/><path d="M0.5,4 H7.5 M4,0.5 C2.5,2.5 2.5,5.5 4,7.5 M4,0.5 C5.5,2.5 5.5,5.5 4,7.5" fill="none" stroke="var(--white)" stroke-width="0.6"/></svg>
        www.hearthmile.example
      </li>
    </ul>

    <div class="licence">
      <p>NMLS 61947</p>
      <p>Company NMLS 274615</p>
    </div>
  </section>

  <section class="card card--back">
    <p class="brand--back">HearthMile</p>
  </section>
</main>
</body>
</html>
```